Tallow Crest - Facebook Cover Photo & Photo Icon Design

We’re looking for a Facebook Cover Photo and Profile Icon design for Tallow Crest, a leading Residential Real Estate brand under Kestmore Property Agents, based in Capalaba and Alexandra Hills, Queensland, Australia.

This design will represent my professional real estate profile and needs to be bold, clean, and on-brand.

Deliverables:

Facebook Cover Photo (820 x 312 px, optimized for mobile + desktop)

Facebook Profile Icon (1:1 ratio, minimum 320 x 320 px)

Design Guidelines:

1. Must Include:

The Tallow Crest logo (provided after project start)

Use of the Kestmore Property Agents brand colour palette (will be supplied)

Clear connection to residential real estate

2. Optional but Preferred:

A local photo or skyline of Capalaba or Alexandra Hills in QLD (bonus points for this)

Space for a short tagline like:
“Selling Faster. Selling Smarter. Selling Kestmore.”
(Optional tagline – open to variations if it improves layout/design)

3. Style & Feel:

Professional yet personable

Clean, modern aesthetic

Subtle touches of fun or personality are welcome

Layout must work well when overlaid by Facebook UI elements (like profile photo & call-to-action buttons)

Who I Am:
I'm a well-known residential real estate agent in the Redlands area, known for high-energy campaigns, premium video marketing, and a results-driven approach. My brand is fun, fresh, and high-performing — just like the real estate campaigns I run.

Files to be Provided (after selection):

Tallow Crest logo in high-res

Brand colour palette / style reference

Optional photo references if local imagery is not sourced by designer

Final Notes:

Make sure all text is legible on mobile and desktop

Original, layered design files must be delivered (PSD or AI preferred)

Bonus points if it feels uniquely “Bayside Queensland” while maintaining a national-level professional polish

Target Market(s)

Alexandra Hills, Capalaba & Sheldon

Industry/Entity Type

Real Estate

Colors
0054AA
0677BA
7BADD7
CADEEF
E8F1F8

Requirements
Must have
• Headshot, Mobile Number 0417 962 085, Suburbs - Alexandra Hills, Capalaba & Sheldon
Nice to have
• White, Crisp & Professional. Bottom Banner with Suburb List. Specialising in Alexandra Hills, Capalaba & Sheldon

```html
<!DOCTYPE html>
<html lang="en">
<head>
<meta charset="utf-8">
<title>Tallow Crest – Facebook Cover &amp; Profile Icon</title>
<link rel="stylesheet" href="https://fonts.googleapis.com/css2?family=Quicksand:wght@400;600;700&family=Roboto+Condensed:wght@700&display=swap">
<style>
  :root {
    --stage: #ecebe8;
    --navy-deep: #17305f;
    --navy-mid: #2a4f8c;
    --navy-text: #1c2466;
    --tan: #d8a96a;
    --white: #ffffff;
    --sky-top: #8fb8e0;
    --sky-low: #c9dcec;
    --sea: #5f8fb4;
    --suburb-green: #5d7a4e;
    --suburb-roof: #8d8a7c;
    --suit: #2b3a52;
  }
  * { margin: 0; padding: 0; box-sizing: border-box; }
  html, body { width: 1200px; height: 447px; overflow: hidden; }
  body {
    background: var(--stage);
    position: relative;
    font-family: "Quicksand", sans-serif;
  }

  /* Cover photo 820 x 312 */
  .cover {
    position: absolute;
    left: 53px; top: 40px;
    width: 776px; height: 295px;
    overflow: hidden;
  }
  .cover-aerial {
    position: absolute; left: 295px; top: 0;
    width: 481px; height: 295px;
    background: linear-gradient(180deg, var(--sky-top) 0%, var(--sky-low) 22%, var(--sea) 27%, var(--suburb-roof) 40%, var(--suburb-green) 70%, var(--suburb-green) 100%);
  }
  .cover-headshot {
    position: absolute; left: 540px; top: 25px;
    width: 236px; height: 270px;
    background: linear-gradient(180deg, rgba(43,58,82,0) 0%, rgba(43,58,82,0.55) 38%, var(--suit) 60%, var(--suit) 100%);
    border-radius: 90px 90px 0 0;
  }
  .cover-message {
    position: absolute; left: 0; top: 0;
    width: 295px; height: 147px;
    background: linear-gradient(180deg, var(--navy-mid) 0%, var(--navy-deep) 100%);
    color: var(--white);
  }
  .cover-message .tagline {
    position: absolute; left: 14px; top: 18px;
    font-size: 15.5px; font-weight: 600; line-height: 26px;
  }
  .cover-message .phone {
    position: absolute; left: 14px; top: 104px;
    display: flex; align-items: center; gap: 8px;
    font-size: 28px; font-weight: 700; letter-spacing: 0.3px;
  }
  .cover-brand {
    position: absolute; left: 0; top: 147px;
    width: 295px; height: 148px;
    background: var(--tan);
    color: var(--navy-text);
  }
  .brand-name {
    font-family: "Quicksand", sans-serif;
    font-weight: 400;
    color: var(--navy-text);
    letter-spacing: 2px;
    line-height: 1;
  }
  .cover-brand .brand-name {
    position: absolute; left: 14px; top: 42px;
    font-size: 30px;
  }
  .cover-brand .agent {
    position: absolute; left: 14px; top: 113px;
    font-size: 15.5px; font-weight: 700;
  }

  /* Profile icon 320 x 320 */
  .profile {
    position: absolute;
    left: 848px; top: 39px;
    width: 303px; height: 303px;
    overflow: hidden;
  }
  .profile-message {
    position: absolute; left: 0; top: 0;
    width: 303px; height: 151px;
    background: linear-gradient(180deg, var(--navy-mid) 0%, var(--navy-deep) 100%);
    color: var(--white);
    text-align: center;
  }
  .profile-message .tagline {
    position: absolute; left: 0; right: 0; top: 18px;
    font-size: 16px; font-weight: 600; line-height: 29px;
  }
  .profile-message .phone {
    position: absolute; left: 22px; top: 78px;
    display: flex; align-items: center; gap: 10px;
    font-size: 27px; font-weight: 700;
  }
  .profile-brand {
    position: absolute; left: 0; top: 151px;
    width: 303px; height: 152px;
    background: var(--tan);
  }
  .profile-brand .brand-name {
    position: absolute; left: 8px; top: 16px;
    font-size: 26px; line-height: 31px;
  }
  .profile-brand .agent {
    position: absolute; left: 8px; top: 96px;
    font-family: "Roboto Condensed", sans-serif;
    font-weight: 700; font-size: 15px; line-height: 21px;
    color: var(--navy-text);
  }
  .profile-headshot {
    position: absolute; left: 150px; top: 127px;
    width: 153px; height: 176px;
    background: linear-gradient(180deg, rgba(43,58,82,0) 0%, rgba(43,58,82,0.5) 35%, var(--suit) 58%, var(--suit) 100%);
    border-radius: 70px 70px 0 0;
  }
  .phone-icon { flex: none; }
</style>
</head>
<body>

  <section class="cover" aria-label="Facebook cover photo">
    <div class="cover-aerial" role="img" aria-label="Aerial photo of Kestmore suburbs stretching to the bay under a blue sky"></div>
    <div class="cover-headshot" role="img" aria-label="Headshot of agent Rory Penhall in a navy blazer and white shirt"></div>

    <div class="cover-message">
      <p class="tagline">Selling Faster. Selling Smarter.<br>Selling Kestmore.</p>
      <p class="phone">
        <svg class="phone-icon" width="34" height="34" viewBox="0 0 34 34" fill="none" stroke="#fff" stroke-width="2" stroke-linecap="round" stroke-linejoin="round">
          <path d="M8 4l5 6-3 4c2 4 5 7 9 9l4-3 6 5-3 5C15 30 4 19 3 7z"/>
          <path d="M20 9a6 6 0 0 1 5 5"/>
          <path d="M20 4a11 11 0 0 1 10 10"/>
        </svg>
        0417 962 085
      </p>
    </div>

    <div class="cover-brand">
      <p class="brand-name">TALLOW CREST</p>
      <p class="agent">Rory Penhall, Suburb Specialist</p>
    </div>
  </section>

  <section class="profile" aria-label="Facebook profile icon">
    <div class="profile-message">
      <p class="tagline">Selling Faster. Selling Smarter.<br>Selling Kestmore.</p>
      <p class="phone">
        <svg class="phone-icon" width="34" height="34" viewBox="0 0 34 34" fill="none" stroke="#fff" stroke-width="2" stroke-linecap="round" stroke-linejoin="round">
          <path d="M8 4l5 6-3 4c2 4 5 7 9 9l4-3 6 5-3 5C15 30 4 19 3 7z"/>
          <path d="M20 9a6 6 0 0 1 5 5"/>
          <path d="M20 4a11 11 0 0 1 10 10"/>
        </svg>
        0417 962 085
      </p>
    </div>
    <div class="profile-brand">
      <p class="brand-name">TALLOW<br>CREST</p>
      <p class="agent">Rory Penhall<br>Suburb Specialist</p>
    </div>
    <div class="profile-headshot" role="img" aria-label="Headshot of agent Rory Penhall in a navy blazer and white shirt"></div>
  </section>

</body>
</html>
```